Website for Apartment Rental in Prague

I would like to create designs of my website focused on luxury apartment rentals in Prague, Czech Republic. I created initial mock-ups, They are all attached. I need to design homepage and subpage. The mock-ups were created by combining elements from different websites that I liked but I need you to create a design that is unique and original. The attached files a only a guidance for the structure of the website but not for the design. Try to be creative.

Apartment

```html
<!DOCTYPE html>
<html lang="en">
<head>
<meta charset="utf-8">
<title>Dwellmark Rentals</title>
<link rel="stylesheet" href="https://fonts.googleapis.com/css2?family=Jost:wght@400;500;600&family=Open+Sans:wght@400;600;700&display=swap">
<style>
:root{
  --maroon:#2d1a1f;
  --gold:#ddb04a;
  --ink:#1d1d1d;
  --muted:#6b6b6b;
  --line:#d9d9d9;
  --white:#fff;
  --footer:#1c1c1c;
}
*{box-sizing:border-box;margin:0;padding:0}
html,body{width:1200px;height:3991px;overflow:hidden}
body{background:var(--white);font-family:"Open Sans",sans-serif;color:var(--ink);position:relative}
.abs{position:absolute}

/* header */
.topbar{top:0;left:0;width:1200px;height:80px}
.brand{left:88px;top:22px;font-family:"Jost",sans-serif;font-weight:600;font-size:30px;color:var(--gold);letter-spacing:.5px}
.contacts{right:70px;top:28px;display:flex;gap:26px;font-size:15px;color:var(--ink)}
.contacts span{display:flex;align-items:center;gap:10px}
.ico{width:24px;height:24px;border-radius:50%;background:var(--maroon);display:inline-flex;align-items:center;justify-content:center}
.nav{top:80px;left:0;width:1200px;height:40px;background:var(--maroon);display:flex;padding-left:88px}
.nav a{color:#fff;text-decoration:none;font-family:"Jost",sans-serif;font-size:15px;line-height:40px;margin-right:44px}
.nav a.active{color:var(--gold)}

/* hero */
.hero{top:120px;left:0;width:1200px;height:520px;background:
  linear-gradient(90deg,rgba(255,255,255,.25) 0%,rgba(255,255,255,0) 20%,rgba(255,255,255,0) 80%,rgba(255,255,255,.25) 100%),
  linear-gradient(180deg,#dfe2e4 0%,#b8bcc0 40%,#8d8a86 72%,#c9b59a 86%,#5a4f47 100%)}
.hero h1{position:absolute;top:222px;width:100%;text-align:center;font-family:"Jost",sans-serif;font-weight:600;font-size:50px;color:#fff;letter-spacing:1px}

/* booking */
.booking{top:582px;left:118px;width:962px;height:258px;background:#fff;box-shadow:0 4px 18px rgba(0,0,0,.12)}
.badge{position:absolute;left:0;top:0;width:164px;height:258px;background:var(--gold);color:#fff;text-align:center;padding-top:36px;font-family:"Jost",sans-serif}
.badge .shield{width:56px;height:64px;margin:0 auto 12px;display:block}
.badge .big{font-size:50px;line-height:50px;font-weight:500}
.badge .sm{font-size:18px}
.badge .gt{font-size:20px;color:var(--maroon);font-weight:600}
.form{position:absolute;left:208px;top:22px;width:720px;font-size:13px}
.field{position:absolute;border-bottom:1px solid var(--line);height:52px}
.field label{display:block;font-weight:600;margin-bottom:10px}
.field .v{font-size:13px;color:#333}
.check-btn{position:absolute;left:208px;top:198px;width:340px;height:46px;background:var(--maroon);color:#fff;font-family:"Jost",sans-serif;font-size:16px;text-align:center;line-height:46px;border-radius:2px}

/* section titles */
.sec-title{left:0;width:1200px;text-align:center;font-family:"Jost",sans-serif;font-weight:500;font-size:42px;color:var(--ink)}
.sec-sub{left:0;width:1200px;text-align:center;font-size:13px;color:var(--muted)}
.sec-sub i{display:block;width:120px;height:1px;background:var(--line);margin:0 auto 4px}

/* services */
.service{top:990px;width:220px;text-align:center}
.service .ph{width:206px;height:206px;border-radius:50%;margin:0 auto;border:5px solid #e8e8e8;box-shadow:0 6px 10px rgba(0,0,0,.15)}
.service.featured .ph{border-color:var(--gold)}
.service p{margin-top:24px;font-family:"Jost",sans-serif;font-size:21px;line-height:26px}
.service.featured p{color:var(--gold)}

/* split about */
.about-img{top:1315px;left:0;width:760px;height:447px;background:linear-gradient(180deg,#f0ece6 0%,#e3dcd3 45%,#b7aca2 70%,#6f6660 100%)}
.about-card{top:1315px;left:650px;width:550px;height:447px;background:#fff;border-radius:300px 0 0 300px / 447px 0 0 447px}
.about-card h2{position:absolute;left:104px;top:96px;width:400px;text-align:center;font-family:"Jost",sans-serif;font-weight:500;font-size:28px;color:var(--gold)}
.about-card h2 b{color:var(--ink);font-weight:500}
.about-card h3{position:absolute;left:104px;top:142px;width:400px;text-align:center;font-size:12px;font-weight:600;color:#555;border-bottom:1px solid var(--line);padding-bottom:6px}
.about-card p{position:absolute;left:124px;top:176px;width:360px;text-align:center;font-size:11.5px;line-height:19px;color:var(--muted)}

/* help band */
.help{top:1762px;left:0;width:1200px;height:158px;background:var(--maroon)}
.help h2{position:absolute;left:86px;top:42px;font-family:"Jost",sans-serif;font-weight:500;font-size:36px;color:#fff}
.help p{position:absolute;left:86px;top:94px;font-size:15px;color:#e9e2e3}
.help .call{position:absolute;left:924px;top:58px;width:194px;height:44px;background:var(--gold);border-radius:4px;display:flex;align-items:center;justify-content:center;gap:10px;font-size:15px;color:var(--maroon);font-weight:600}

/* map */
.map{top:2045px;left:240px;width:722px;height:368px;background:linear-gradient(160deg,#eef0e4 0%,#dfe6d2 40%,#c9dbe6 62%,#9fc2e0 100%);border:6px solid #f2f2f2;box-shadow:0 2px 8px rgba(0,0,0,.15)}

/* featured grid */
.grid{top:2560px;left:0;width:1200px;height:445px;display:grid;grid-template-columns:repeat(4,300px);grid-template-rows:repeat(2,222.5px)}
.tile{position:relative}
.t1{background:linear-gradient(180deg,#e8e4de,#b4aa9e 60%,#6f655c)}
.t2{background:linear-gradient(180deg,#8fb9e0 0%,#b7cde0 35%,#c98a5d 60%,#8a5a3c)}
.t3{background:linear-gradient(135deg,#5d5c5a,#2e2c2b)}
.t4{background:linear-gradient(180deg,#f1f2f3,#c4c8cc 55%,#6f7378)}
.t5{background:linear-gradient(180deg,#a9c8e4 0%,#c9c3b8 45%,#5d5a58)}
.t6{background:linear-gradient(180deg,#eef1f3 0%,#b8cfe0 50%,#d9c7ad)}
.t7{background:linear-gradient(180deg,#fafafa,#d5d5d5 60%,#9a9a9a)}
.t8{background:linear-gradient(180deg,#9cc3e6 0%,#c8d7e6 35%,#b98a5a 65%,#6e4f35)}
.overlay{position:absolute;left:18px;top:14px;width:264px;height:194px;background:rgba(30,20,22,.72);color:#fff;text-align:center;padding-top:24px}
.overlay h4{font-family:"Jost",sans-serif;font-weight:500;font-size:21px}
.overlay .rate{font-size:14px;margin-top:10px;color:#eee}
.overlay .x{font-size:11.5px;color:#ccc;margin-top:10px;line-height:15px;padding:0 20px}
.overlay .btn{display:inline-flex;align-items:center;gap:6px;margin-top:12px;border:1px solid #fff;padding:4px 12px;font-size:13px}
.overlay .btn i{width:18px;height:18px;border-radius:50%;background:var(--gold);display:inline-block}
.search{top:3005px;left:0;width:1200px;height:66px;background:var(--maroon);display:flex;align-items:center;justify-content:center;gap:14px;color:#fff;font-family:"Jost",sans-serif;font-size:20px}

/* news */
.lead{top:3212px;left:88px;width:1024px;text-align:center;font-size:13px;line-height:19px;color:#444}
.card{top:3268px;width:318px}
.card .ph{position:relative;height:192px}
.card .date{position:absolute;right:0;top:0;background:var(--maroon);color:#fff;font-size:12px;padding:6px 12px}
.card h5{margin-top:20px;font-family:"Jost",sans-serif;font-weight:600;font-size:18px;line-height:24px}
.card p{margin-top:12px;font-size:12px;line-height:19px;color:#555}

/* footer */
.footer{top:3645px;left:0;width:1200px;height:346px;background:var(--footer);color:#ddd}
.footer h6{position:absolute;top:40px;font-family:"Jost",sans-serif;font-weight:500;font-size:18px;color:#fff}
.footer h6::after{content:"";display:block;width:48px;height:2px;background:var(--gold);margin-top:8px}
.links{position:absolute;top:90px;font-size:13px;line-height:23px;list-style:none}
.links li::before{content:"› ";color:var(--gold)}
.input{position:absolute;left:362px;width:184px;height:28px;background:#fff;font-size:10px;color:#999;padding:7px 8px}
.submit{position:absolute;left:362px;top:232px;width:96px;height:28px;background:var(--gold);color:var(--maroon);font-size:12px;text-align:center;line-height:28px;font-weight:600}
.info{position:absolute;left:615px;top:90px;width:260px;font-size:12.5px;line-height:18px}
.info div{display:flex;gap:12px;margin-bottom:14px}
.info svg{flex:none;margin-top:2px}
.fbrand{position:absolute;left:912px;top:120px;font-family:"Jost",sans-serif;font-size:20px;font-weight:500;color:var(--gold)}
.social{position:absolute;left:960px;top:158px;display:flex;gap:8px}
.social i{width:26px;height:26px;border-radius:50%;background:#2f7fc0;display:block}
.copy{position:absolute;left:0;top:320px;width:1200px;text-align:center;font-size:11px;color:#aaa}
</style>
</head>
<body>

<header class="abs topbar">
  <div class="abs brand">DWELLMARK RENTALS</div>
  <div class="abs contacts">
    <span><i class="ico"><svg width="12" height="12" viewBox="0 0 24 24"><path fill="#fff" d="M6.6 10.8a15.1 15.1 0 006.6 6.6l2.2-2.2c.3-.3.7-.4 1-.2 1.1.4 2.3.6 3.6.6.6 0 1 .4 1 1V20c0 .6-.4 1-1 1A17 17 0 013 4c0-.6.4-1 1-1h3.5c.6 0 1 .4 1 1 0 1.3.2 2.5.6 3.6.1.3 0 .7-.2 1z"/></svg></i>(555) 204 - 3187</span>
    <span><i class="ico"><svg width="12" height="12" viewBox="0 0 24 24"><path fill="#fff" d="M2 5h20v14H2z"/><path fill="none" stroke="#2d1a1f" stroke-width="2" d="M2 5l10 8 10-8"/></svg></i>info@dwellmarkrentals.com</span>
  </div>
</header>

<nav class="abs nav">
  <a class="active">Home</a><a>Apartments</a><a>Location</a><a>Services</a><a>Gallery</a><a>News</a><a>Exclusive Offers &amp; Tours</a><a>For Families</a><a>Contact Us</a>
</nav>

<section class="abs hero" role="img" aria-label="Bright modern interior with rows of desks and chairs">
  <h1>BEING HOME DWELLMARK</h1>
</section>

<section class="abs booking">
  <div class="badge">
    <svg class="shield" viewBox="0 0 56 64"><path d="M28 3l22 8v18c0 15-10 26-22 32C16 55 6 44 6 29V11z" fill="none" stroke="#fff" stroke-width="3"/><path d="M18 33l7 7 13-14" fill="none" stroke="#fff" stroke-width="3"/></svg>
    <div class="big">BEST</div><div class="sm">PRICE</div><div class="gt">GUARANTEED</div>
  </div>
  <div class="form">
    <div class="field" style="left:0;top:0;width:340px"><label>Check in date :</label><span class="v">20 / 10 / 2017</span></div>
    <div class="field" style="left:370px;top:0;width:350px"><label>Check Out date :</label><span class="v">20 / 10 / 2017</span></div>
    <div class="field" style="left:0;top:72px;width:100px"><label>Adults</label><span class="v">2</span></div>
    <div class="field" style="left:120px;top:72px;width:100px"><label>Children</label><span class="v">1</span></div>
    <div class="field" style="left:240px;top:72px;width:100px"><label>Infonts</label><span class="v">0</span></div>
    <div class="field" style="left:370px;top:72px;width:350px"><label>Promotional code</label></div>
    <div style="position:absolute;left:370px;top:150px">or</div>
    <div class="field" style="left:370px;top:170px;width:350px;height:40px;padding-top:12px"><span class="v">Select Rental Unit</span></div>
  </div>
  <div class="check-btn">Check Availability</div>
</section>

<h2 class="abs sec-title" style="top:890px">Services</h2>
<div class="abs sec-sub" style="top:942px"><i></i>We Provide</div>

<div class="abs service" style="left:108px"><div class="ph" role="img" aria-label="Furnished living room" style="background:linear-gradient(180deg,#e6e0d8,#a89c90 60%,#5e544c)"></div><p>Exclusive<br>Rental Choices</p></div>
<div class="abs service featured" style="left:362px"><div class="ph" role="img" aria-label="Couple saving money for a home" style="background:linear-gradient(135deg,#f4efe9,#d7c1ad 55%,#9a7c66)"></div><p>Budget<br>Friendly homes</p></div>
<div class="abs service" style="left:618px"><div class="ph" role="img" aria-label="Glass commercial building" style="background:linear-gradient(180deg,#cfe0ef,#8fb1d0 45%,#44586a)"></div><p>Commercial<br>Properties</p></div>
<div class="abs service" style="left:872px"><div class="ph" role="img" aria-label="Hand holding house keys" style="background:linear-gradient(135deg,#6c7a90,#2c3444 60%,#161b25)"></div><p>Rental<br>Assistance</p></div>

<div class="abs about-img" role="img" aria-label="White living room with sofa, shelves and pendant lamp"></div>
<section class="abs about-card">
  <h2>Dwellmark <b>Rentals</b></h2>
  <h3>Lorem ipsum dolor sit amet, consectetuer</h3>
  <p>Lorem ipsum dolor sit amet, consectetuer adipiscing elit, sed diam nonummy nibh euismod tincidunt ut laoreet dolore magna aliquam erat volutpat. Ut wisi enim ad minim veniam, quis nostrud exerci tation ullamcorper suscipit lobortis nisl ut aliquip ex ea commodo consequat. Duis autem vel eum iriure dolor in hendrerit in vulputate velit esse molestie consequat, vel illum dolore eu feugiat nulla facilisis at vero eros et accumsan et iusto odio dignissim qui blandit praesent luptatum zzril delenit augue duis dolore te feugait nulla facilisi.</p>
</section>

<section class="abs help">
  <h2>Do You Need Help with Dwellmark Rentals</h2>
  <p>Lorem ipsum dolor sit amet, consectetuer adipiscing elit, sed diam nonummy nibh euismod</p>
  <div class="call"><svg width="16" height="16" viewBox="0 0 24 24"><path fill="#2d1a1f" d="M6.6 10.8a15.1 15.1 0 006.6 6.6l2.2-2.2c.3-.3.7-.4 1-.2 1.1.4 2.3.6 3.6.6.6 0 1 .4 1 1V20c0 .6-.4 1-1 1A17 17 0 013 4c0-.6.4-1 1-1h3.5c.6 0 1 .4 1 1 0 1.3.2 2.5.6 3.6.1.3 0 .7-.2 1z"/></svg>(555)204 - 3187</div>
</section>

<h2 class="abs sec-title" style="top:1972px">Location</h2>
<div class="abs map" role="img" aria-label="Map of the region with property location markers"></div>

<h2 class="abs sec-title" style="top:2455px">Featured Property</h2>
<div class="abs sec-sub" style="top:2510px"><i></i>Our Product Type</div>

<section class="abs grid">
  <div class="tile t1" role="img" aria-label="Modern kitchen"></div>
  <div class="tile t2" role="img" aria-label="Apartment buildings"></div>
  <div class="tile t3" role="img" aria-label="Featured property interior">
    <div class="overlay">
      <h4>2140-2298 Linden Ave.</h4>
      <div class="rate">Lease Rate: Call For Details</div>
      <div class="x">Lorem ipsum dolor sit amet, consectetuer adipiscing elit</div>
      <div class="btn"><i></i>Know More</div>
    </div>
  </div>
  <div class="tile t4" role="img" aria-label="Office space"></div>
  <div class="tile t5" role="img" aria-label="Residential tower"></div>
  <div class="tile t6" role="img" aria-label="Living room with large windows"></div>
  <div class="tile t7" role="img" aria-label="White open-plan office"></div>
  <div class="tile t8" role="img" aria-label="Brick townhouses"></div>
</section>
<div class="abs search"><svg width="22" height="22" viewBox="0 0 24 24"><circle cx="10" cy="10" r="7" fill="none" stroke="#fff" stroke-width="2.5"/><path d="M15 15l6 6" stroke="#fff" stroke-width="2.5"/></svg>Search Here...</div>

<h2 class="abs sec-title" style="top:3118px">Latest New</h2>
<div class="abs sec-sub" style="top:3172px"><i></i>From Rentals</div>
<p class="abs lead">Lorem ipsum dolor sit amet, consectetuer adipiscing elit, sed diam nonummy nibh euismod tincidunt ut laoreet dolore magna aliquam erat volutpat. Ut wisi enim ad minim veniam, quis nostrud exerci tation ullamcorper suscipit lobortis nisl ut aliquip ex ea commodo consequat.</p>

<article class="abs card" style="left:88px"><div class="ph" role="img" aria-label="Agent showing a home to a couple" style="background:linear-gradient(180deg,#eeeae4,#c5bcb2 55%,#7b726b)"><span class="date">21, Nov 2017</span></div><h5>Lorem ipsum dolor sit consectetuer adipiscing elit</h5><p>sed diam nonummy nibh euismod tincidunt ut laoreet dolore magna aliquam erat volutpat. Ut wisi enim ad minim veniam, quis nostrud exerci tation...[+]</p></article>
<article class="abs card" style="left:441px"><div class="ph" role="img" aria-label="Handing over house keys" style="background:linear-gradient(135deg,#f6f6f6,#e2d6cc 55%,#b09684)"><span class="date">21, Nov 2017</span></div><h5>Lorem ipsum dolor sit consectetuer adipiscing elit</h5><p>sed diam nonummy nibh euismod tincidunt ut laoreet dolore magna aliquam erat volutpat. Ut wisi enim ad minim veniam, quis nostrud exerci tation...[+]</p></article>
<article class="abs card" style="left:794px"><div class="ph" role="img" aria-label="Modern apartment block" style="background:linear-gradient(180deg,#9fc4e6 0%,#cbd9e6 40%,#b0764e 70%,#7a5238)"><span class="date">21, Nov 2017</span></div><h5>Lorem ipsum dolor sit consectetuer adipiscing elit</h5><p>sed diam nonummy nibh euismod tincidunt ut laoreet dolore magna aliquam erat volutpat. Ut wisi enim ad minim veniam, quis nostrud exerci tation...[+]</p></article>

<footer class="abs footer">
  <h6 style="left:88px">Quick Links</h6>
  <ul class="links" style="left:94px"><li>Home</li><li>Apartments</li><li>Location</li><li>Services</li><li>Gallery</li><li>News</li></ul>
  <ul class="links" style="left:186px"><li>Exclusive Offers</li><li>&nbsp;&nbsp;&amp; Tours</li><li>For Families</li><li>Contact Us</li></ul>
  <h6 style="left:362px">Contact Now</h6>
  <div class="input" style="top:105px">Your Name</div>
  <div class="input" style="top:140px">Your Email</div>
  <div class="input" style="top:175px;height:48px">Message</div>
  <div class="submit">SUBMIT</div>
  <h6 style="left:615px">Contact Information</h6>
  <div class="info">
    <div><svg width="14" height="16" viewBox="0 0 24 28"><path fill="#fff" d="M12 0a10 10 0 0110 10c0 8-10 18-10 18S2 18 2 10A10 10 0 0112 0zm0 6a4 4 0 100 8 4 4 0 000-8z"/></svg><span><b>Dwellmark Rentals</b><br>1200 Elm Court, 3rd floor, Springvale 00000</span></div>
    <div><svg width="14" height="14" viewBox="0 0 24 24"><path fill="#fff" d="M6.6 10.8a15.1 15.1 0 006.6 6.6l2.2-2.2c.3-.3.7-.4 1-.2 1.1.4 2.3.6 3.6.6.6 0 1 .4 1 1V20c0 .6-.4 1-1 1A17 17 0 013 4c0-.6.4-1 1-1h3.5c.6 0 1 .4 1 1 0 1.3.2 2.5.6 3.6.1.3 0 .7-.2 1z"/></svg><span>+ 555-2043-187</span></div>
    <div><svg width="14" height="14" viewBox="0 0 24 24"><rect x="3" y="6" width="18" height="14" fill="#fff"/><rect x="6" y="2" width="12" height="5" fill="#fff"/></svg><span>5552043188</span></div>
    <div><svg width="14" height="14" viewBox="0 0 24 24"><path fill="#fff" d="M2 5h20v14H2z"/><path fill="none" stroke="#1c1c1c" stroke-width="2" d="M2 5l10 8 10-8"/></svg><span>info@dwellmarkrentals.com</span></div>
  </div>
  <div class="fbrand">Dwellmark Rentals</div>
  <div class="social"><i></i><i></i><i></i></div>
  <div class="copy">© 2017 Dwellmark Rentals. All Rights Reserved.</div>
</footer>

</body>
</html>
```